Brimsett Gardening Fresh New Website

We are looking to create a simple fresh website for our landscaping business. The website should appeal to a 'high end' audience. We deal with a lot of Embassies and affluent clients who have extremely large gardens that are meticulously maintained. The site is about communicating our excellent landscaping and customer service skills and encouraging new clients to reach out and engage us to take care of their gardens.

The website is basically going to be our business card, it will have almost no functionality other than two 'contact us' forms, one for smaller clients and one for more detailed projects.

The website will not have a lot of written content and will have to show photos of beautifully landscaped gardens.

The main logo in black will influence the site, however, we are open to all suggestions.

We are expecting to have the following pages:
Home Page
Services
About Us
Contact Us
Showcase (photo gallery of our work)

We need someone who can code it to wordpress and be available for minor changes over a number of days. They will be simple tweaks.

```html
<!DOCTYPE html>
<html lang="en">
<head>
<meta charset="utf-8">
<title>Brimsett Gardening</title>
<link href="https://fonts.googleapis.com/css2?family=Poppins:wght@400;500;600;700&display=swap" rel="stylesheet">
<style>
:root{
  --dark:#1e1e1e;
  --gold:#a8752a;
  --gold-soft:#c9a24e;
  --yellow:#f6d54a;
  --text:#333;
  --muted:#555;
  --white:#fff;
  --line:#e4e4e4;
}
*{box-sizing:border-box;margin:0;padding:0}
html,body{width:1200px;height:3331px;overflow:hidden}
body{position:relative;font-family:'Poppins',sans-serif;color:var(--text);background:var(--white)}
.btn{position:absolute;display:flex;align-items:center;justify-content:center;background:var(--gold);color:var(--white);font-size:13px;font-weight:500;text-transform:uppercase;letter-spacing:.2px}
.section-title{position:absolute;left:0;width:1200px;text-align:center;font-size:34px;font-weight:700;color:#1a1a1a;letter-spacing:.3px}
.title-rule{position:absolute;left:575px;width:50px;height:2px;background:var(--gold)}

/* header */
.site-header{position:absolute;left:0;top:0;width:1200px;height:85px;background:var(--dark)}
.brand{position:absolute;left:142px;top:12px;width:90px;text-align:center;color:var(--gold-soft);font-size:12px;font-weight:500;letter-spacing:3px;line-height:16px;text-transform:uppercase}
.brand .dot{display:block;width:14px;height:14px;border:1.5px solid var(--gold-soft);border-radius:50%;margin:0 auto 4px}
.nav a{position:absolute;top:32px;font-size:13px;color:var(--white);text-decoration:none;transform:translateX(-50%)}
.nav a.active{color:var(--yellow);font-weight:600}

/* hero */
.hero{position:absolute;left:0;top:85px;width:1200px;height:550px;background:linear-gradient(180deg,#8fa7b6 0%,#6d7a80 30%,#5b5247 55%,#4f6a2c 75%,#5f8a2a 100%)}
.hero-brand{position:absolute;left:142px;top:256px;width:272px;height:52px;background:var(--white);display:flex;align-items:center;justify-content:center;font-size:23px;font-weight:700;color:#1a1a1a;text-transform:uppercase}
.hero-title{position:absolute;left:142px;top:320px;font-size:38px;line-height:46px;font-weight:700;color:var(--white);text-transform:uppercase;text-shadow:0 2px 6px rgba(0,0,0,.4)}

.inquiry{position:absolute;left:709px;top:107px;width:350px;height:505px;background:rgba(235,235,235,.88)}
.tab{position:absolute;top:0;height:38px;display:flex;align-items:center;justify-content:center;font-size:12px;font-weight:600;text-transform:uppercase}
.tab-small{left:14px;width:170px;background:var(--yellow);color:#1a1a1a;border-radius:0 0 0 30px}
.tab-large{left:184px;width:152px;background:var(--gold);color:var(--white);border-radius:0 0 30px 0}
.inquiry h3{position:absolute;left:0;top:48px;width:350px;text-align:center;font-size:17px;font-weight:600;color:#1a1a1a}
.field{position:absolute;left:19px;width:314px;background:var(--white);border:1px solid #dcdcdc;border-radius:3px;font-size:11px;color:#444;padding:12px 9px}
.field svg{position:absolute;right:10px;top:12px}
.checks{position:absolute;left:19px;top:384px;width:314px;font-size:11px;color:#222}
.check{position:absolute;display:flex;align-items:center;gap:6px;white-space:nowrap}
.box{width:12px;height:12px;border:1px solid #999;background:var(--white)}
.box.on{background:var(--yellow);border-color:#777;display:flex;align-items:center;justify-content:center}

/* about */
.about-visual{position:absolute;left:119px;top:646px;width:486px;height:459px;background:radial-gradient(ellipse at 50% 45%,#c9ccd2 0%,#dfe3e6 45%,#f5f6f6 75%,#fff 100%)}
.about-kicker{position:absolute;left:611px;top:752px;font-size:32px;font-weight:600;color:var(--gold)}
.about-title{position:absolute;left:611px;top:790px;font-size:32px;font-weight:600;color:#1a1a1a}
.about-rule{position:absolute;left:611px;top:842px;width:50px;height:2px;background:var(--gold)}
.about-copy{position:absolute;left:611px;top:862px;width:470px;font-size:13px;line-height:22px;color:var(--muted);white-space:nowrap}
.about-copy p{margin-bottom:6px}

/* services */
.services-bg{position:absolute;left:0;top:1293px;width:1200px;height:707px;background:linear-gradient(180deg,#fff 0%,#e9e4dc 20%,#b9aa93 55%,#6f7a45 85%,#556633 100%)}
.svc-tab{position:absolute;top:1205px;height:36px;display:flex;align-items:center;justify-content:center;font-size:12px;font-weight:500;text-transform:uppercase}
.card{position:absolute;width:300px;height:241px}
.card-photo{position:absolute;left:0;top:0;width:300px;height:241px}
.card-label{position:absolute;left:14px;top:211px;width:272px;height:54px;background:var(--white);display:flex;align-items:center;justify-content:center;gap:8px;font-size:16px;font-weight:600;color:#1a1a1a;box-shadow:0 2px 6px rgba(0,0,0,.08)}
.card-label.featured{background:var(--yellow);height:83px;flex-direction:column;gap:2px}
.card-label.featured .row{display:flex;align-items:center;gap:8px}
.card-label.featured .link{font-size:12px;font-weight:500;text-decoration:underline;margin-left:34px}

/* testimonials */
.t-card{position:absolute;width:300px;background:var(--white);border:1px solid var(--line);padding:20px 18px 0}
.t-card.featured{box-shadow:0 4px 14px rgba(0,0,0,.08);border-bottom:4px solid var(--gold);padding-top:16px}
.t-head{display:flex;align-items:center;gap:12px;margin-bottom:20px}
.avatar{width:58px;height:58px;border-radius:50%;flex:none}
.t-name{font-size:16px;font-weight:500;color:#1a1a1a;line-height:20px}
.stars{color:#f2c21b;font-size:13px;letter-spacing:2px}
.t-text{font-size:12.8px;line-height:22px;color:var(--muted);white-space:nowrap}
.arrow{position:absolute;width:42px;height:42px;border-radius:50%;background:var(--white);box-shadow:0 2px 8px rgba(0,0,0,.15);display:flex;align-items:center;justify-content:center}

/* gallery */
.shot{position:absolute;top:2600px;width:234px;height:246px}

/* footer */
.site-footer{position:absolute;left:0;top:2992px;width:1200px;height:339px;background:var(--dark);color:var(--white)}
.footer-brand{position:absolute;left:110px;top:62px;width:220px;text-align:center;color:var(--gold-soft);font-size:22px;font-weight:500;letter-spacing:6px;line-height:28px;text-transform:uppercase}
.footer-brand .dot{display:block;width:34px;height:34px;border:2px solid var(--gold-soft);border-radius:50%;margin:0 auto 12px}
.social{position:absolute;top:230px;width:27px;height:27px;border:1.5px solid var(--white);border-radius:50%}
.f-head{position:absolute;top:52px;font-size:15px;font-weight:600;text-transform:uppercase}
.f-rule{position:absolute;top:80px;height:1px;background:var(--gold)}
.f-link{position:absolute;left:512px;font-size:13px}
.contact{position:absolute;left:848px;display:flex;gap:10px;font-size:13px;line-height:19px}
.contact b{font-weight:600;display:block}
.f-divider{position:absolute;left:142px;top:298px;width:917px;height:1px;background:#444}
.copyright{position:absolute;left:0;top:311px;width:1200px;text-align:center;font-size:12.5px}
</style>
</head>
<body>

<header class="site-header">
  <div class="brand"><span class="dot"></span>Brimsett<br>Gardening</div>
  <nav class="nav">
    <a class="active" style="left:452px">Home</a>
    <a style="left:542px">About Us</a>
    <a style="left:639px">Services</a>
    <a style="left:728px">Gallery</a>
    <a style="left:826px">Contact Us</a>
  </nav>
  <div class="btn" style="left:905px;top:25px;width:154px;height:33px">Request a Quote</div>
</header>

<section class="hero" role="img" aria-label="Photo of a craftsman-style house with a manicured lawn and shrub beds"></section>
<div class="hero-brand">Brimsett Gardening</div>
<h1 class="hero-title">Your Full Landscaping<br>&amp; Lawn Care Experts</h1>
<div class="btn" style="left:142px;top:430px;width:153px;height:30px">Request a Quote</div>

<form class="inquiry">
  <div class="tab tab-small">Smaller Clients</div>
  <div class="tab tab-large">Large Clients</div>
  <h3>QUICK INQUIRY</h3>
  <div class="field" style="top:83px;height:40px">Name
    <svg width="14" height="14" viewBox="0 0 14 14" fill="none" stroke="#c9a24e" stroke-width="1.2"><circle cx="7" cy="4.5" r="3"/><path d="M1.5 13c.6-3 2.8-4.5 5.5-4.5s4.9 1.5 5.5 4.5"/></svg></div>
  <div class="field" style="top:131px;height:40px">Email
    <svg width="14" height="14" viewBox="0 0 14 14" fill="none" stroke="#c9a24e" stroke-width="1.2"><rect x="1.5" y="3" width="11" height="9"/><path d="M1.5 3l5.5 5 5.5-5"/></svg></div>
  <div class="field" style="top:180px;height:40px">Phone
    <svg width="14" height="14" viewBox="0 0 14 14" fill="none" stroke="#c9a24e" stroke-width="1.2"><path d="M3 1.5l2.5 2.8-1.3 1.7c.9 1.8 2.1 3 3.8 3.8l1.7-1.3 2.8 2.5-1.4 1.6C6.5 12.6 1.4 7.5 1.4 3z"/></svg></div>
  <div class="field" style="top:227px;height:40px">Service Type
    <svg width="10" height="10" viewBox="0 0 10 10" fill="none" stroke="#555" stroke-width="1.2" style="top:15px"><path d="M2 3.5l3 3 3-3"/></svg></div>
  <div class="field" style="top:274px;height:90px">Message</div>
  <div class="checks">
    <div class="check" style="left:0;top:0"><span class="box"></span>Weekly Lawn Maintenance</div>
    <div class="check" style="left:198px;top:0"><span class="box"></span>Spring Clean Up</div>
    <div class="check" style="left:0;top:20px"><span class="box on"><svg width="9" height="9" viewBox="0 0 9 9" fill="none" stroke="#222" stroke-width="1.4"><path d="M1.5 4.5l2 2 4-4.5"/></svg></span>Fertilizer / Weed Control</div>
    <div class="check" style="left:198px;top:20px"><span class="box"></span>Fall Clean Up</div>
    <div class="check" style="left:0;top:40px"><span class="box"></span>Core Aeration</div>
  </div>
  <div class="btn" style="left:19px;top:450px;width:314px;height:39px;font-size:15px">Submit</div>
</form>

<section class="about">
  <div class="about-visual" role="img" aria-label="Faded photo of a white two-storey house with porch and lawn"></div>
  <div class="about-kicker">ABOUT</div>
  <h2 class="about-title">BRIMSETT GARDENING</h2>
  <div class="about-rule"></div>
  <div class="about-copy">
    <p>Duis aute irure dolor in reprehenderit in voluptate velit esse cillum<br>dolore eu fugiat nulla pariatur.</p>
    <p>Lorem ipsum dolor sit amet, consectetur adipiscing elit, sed do amit<br>eiusmod tempor incididunt ut labore et dolore magna aliqua. Ut enim<br>ad minim veniam, quis nostrud exercitation ullamco laboris nisi ut<br>aliquip ex ea commodo consequat.</p>
  </div>
  <div class="btn" style="left:610px;top:1020px;width:154px;height:34px">Read More</div>
</section>

<section class="services">
  <div class="services-bg" role="img" aria-label="Soft background photo of a garden with stone bench and trees"></div>
  <h2 class="section-title" style="top:1128px">OUR SERVICES</h2>
  <div class="title-rule" style="top:1182px"></div>
  <div class="svc-tab" style="left:434px;width:158px;background:var(--yellow);color:#1a1a1a">Landscape Service</div>
  <div class="svc-tab" style="left:606px;width:159px;background:var(--gold);color:var(--white)">Lawn Service</div>

  <div class="card" style="left:141px;top:1272px">
    <div class="card-photo" role="img" aria-label="Photo of a large estate lawn with rounded trees" style="background:linear-gradient(180deg,#7fa6d4 0%,#b8cde2 30%,#3f6b2b 55%,#6fa33a 100%)"></div>
    <div class="card-label"><svg width="36" height="36" viewBox="0 0 36 36" fill="none" stroke="#1a1a1a" stroke-width="2"><rect x="4" y="4" width="28" height="28"/><path d="M4 18h14M18 4v28"/></svg>Design Service</div>
  </div>
  <div class="card" style="left:450px;top:1272px">
    <div class="card-photo" role="img" aria-label="Photo of a garden patio with a stone fountain" style="background:linear-gradient(180deg,#6a8a4a 0%,#4e6b34 45%,#9a9389 75%,#7d7a70 100%)"></div>
    <div class="card-label featured">
      <div class="row"><svg width="44" height="34" viewBox="0 0 44 34" fill="none" stroke="#1a1a1a" stroke-width="2"><path d="M2 6h6l6 16h20l4-12H12"/><circle cx="16" cy="28" r="4"/><circle cx="34" cy="28" r="4"/></svg>Mulch or Rock Install</div>
      <div class="link">Request A Quote &rarr;</div>
    </div>
  </div>
  <div class="card" style="left:759px;top:1272px">
    <div class="card-photo" role="img" aria-label="Photo of a garden trowel and pots in soil" style="background:linear-gradient(160deg,#5b4333 0%,#3e2c21 60%,#4a3628 100%)"></div>
    <div class="card-label"><svg width="36" height="36" viewBox="0 0 36 36" fill="none" stroke="#1a1a1a" stroke-width="2"><path d="M6 32l10-10M14 20l8-14 6 6-14 8z"/><path d="M4 32h26"/></svg>Grading Rough</div>
  </div>

  <div class="card" style="left:141px;top:1588px">
    <div class="card-photo" role="img" aria-label="Photo of a white manor house behind a broad lawn" style="background:linear-gradient(180deg,#b9cbd8 0%,#4a6b36 35%,#5d8a32 70%,#76a83c 100%)"></div>
    <div class="card-label"><svg width="30" height="36" viewBox="0 0 30 36" fill="none" stroke="#1a1a1a" stroke-width="2"><rect x="3" y="5" width="24" height="28"/><path d="M8 13h14M8 19h14M8 25h10"/></svg>Grading Final</div>
  </div>
  <div class="card" style="left:450px;top:1588px">
    <div class="card-photo" role="img" aria-label="Photo of sod rolls being laid on soil" style="background:linear-gradient(180deg,#2f5a8a 0%,#4f7a2f 35%,#7a6a4a 65%,#5a8a2a 100%)"></div>
    <div class="card-label"><svg width="40" height="36" viewBox="0 0 40 36" fill="none" stroke="#1a1a1a" stroke-width="2"><rect x="3" y="6" width="34" height="26"/><circle cx="12" cy="24" r="5"/><path d="M22 14h10M22 20h10"/></svg>Sod Installation</div>
  </div>
  <div class="card" style="left:759px;top:1588px">
    <div class="card-photo" role="img" aria-label="Photo of a stone retaining wall with iron railing" style="background:linear-gradient(180deg,#8a9a8a 0%,#3f5a2f 40%,#2f3a2a 65%,#8a8a84 100%)"></div>
    <div class="card-label"><svg width="50" height="36" viewBox="0 0 50 36" fill="none" stroke="#1a1a1a" stroke-width="2"><rect x="3" y="3" width="44" height="30"/><path d="M3 13h44M3 23h44M18 3v10M32 3v10M10 13v10M25 13v10M40 13v10M18 23v10M32 23v10"/></svg>Retaining Walls</div>
  </div>

  <div class="btn" style="left:522px;top:1877px;width:154px;height:35px">Request a Quote</div>
</section>

<section class="testimonials">
  <h2 class="section-title" style="top:2073px">WHAT OUR CLIENTS SAY</h2>
  <div class="title-rule" style="top:2128px"></div>

  <div class="t-card" style="left:141px;top:2181px;height:267px">
    <div class="t-head"><div class="avatar" role="img" aria-label="Client portrait" style="background:linear-gradient(135deg,#4ba3d8,#9fd3ee)"></div><div><div class="t-name">Owen Carrick</div><div class="stars">★★★★★</div></div></div>
    <p class="t-text">Lorem ipsum dolor sit amet, consectetur<br>adipiscing elit, sed do eiusmod tempor<br>incididunt ut labore et dolore magna<br>aliqua. Ut enim ad minim veniam ut aut<br>reiciendis voluptatibus maiores alias ut<br>aut reiciendis voluptatibus.</p>
  </div>
  <div class="t-card featured" style="left:450px;top:2153px;height:275px">
    <div class="t-head"><div class="avatar" role="img" aria-label="Client portrait" style="background:linear-gradient(135deg,#3a2f2a,#b9a899)"></div><div><div class="t-name">Nina Halvers</div><div class="stars">★★★★★</div></div></div>
    <p class="t-text">Sed ut perspiciatis unde omnis iste<br>natus error sit voluptatem accusantium<br>doloremque laudantium, totam rem<br>aperiam, eaque ipsa quae ab illo AMIT<br>inventore veritatis et quasi architecto<br>beatae vitae dicta sunt explicabo. Nemo<br>enim ipsam voluptatem.</p>
  </div>
  <div class="t-card" style="left:759px;top:2181px;height:267px">
    <div class="t-head"><div class="avatar" role="img" aria-label="Client portrait" style="background:linear-gradient(135deg,#1f2a30,#4a5a60)"></div><div><div class="t-name">Theo R</div><div class="stars">★★★★★</div></div></div>
    <p class="t-text">Lorem ipsum dolor sit amet, consectetur<br>adipiscing elit, sed do eiusmod tempor<br>incididunt ut labore et dolore magna<br>aliqua. Ut enim ad minim veniam ut aut<br>reiciendis voluptatibus maiores alias ut<br>aut reiciendis voluptatibus.</p>
  </div>

  <div class="arrow" style="left:76px;top:2313px"><svg width="14" height="14" viewBox="0 0 14 14" fill="none" stroke="#111" stroke-width="2.2"><path d="M9 2L4 7l5 5"/></svg></div>
  <div class="arrow" style="left:1083px;top:2313px"><svg width="14" height="14" viewBox="0 0 14 14" fill="none" stroke="#111" stroke-width="2.2"><path d="M5 2l5 5-5 5"/></svg></div>
</section>

<section class="gallery">
  <h2 class="section-title" style="top:2522px">WORK GALLERY</h2>
  <div class="title-rule" style="top:2577px"></div>
  <div class="shot" style="left:0;background:linear-gradient(180deg,#b8cfe0 0%,#b9a27a 35%,#6d9a3a 60%,#8fb84a 100%)" role="img" aria-label="Photo of houses behind a sunlit lawn"></div>
  <div class="shot" style="left:241px;background:linear-gradient(180deg,#5f8a3a 0%,#a08a6a 35%,#7a6a55 70%,#c9a23a 100%)" role="img" aria-label="Photo of a curved stone wall with flower beds"></div>
  <div class="shot" style="left:483px;background:linear-gradient(180deg,#cfdbe6 0%,#c2b39a 40%,#8a9aa8 60%,#5a7a3a 100%)" role="img" aria-label="Photo of a cottage with a flowering front garden"></div>
  <div class="shot" style="left:724px;background:linear-gradient(180deg,#5a7a3a 0%,#b84a5a 30%,#6a8a3a 55%,#a89a8a 100%)" role="img" aria-label="Photo of a stone garden path between flower beds"></div>
  <div class="shot" style="left:966px;background:linear-gradient(180deg,#c6d3dc 0%,#4f7a34 40%,#3f5a2a 60%,#8a8a7a 100%)" role="img" aria-label="Photo of a checkered paver path to a house"></div>
  <div class="btn" style="left:522px;top:2872px;width:153px;height:34px">View All</div>
</section>

<footer class="site-footer">
  <div class="footer-brand"><span class="dot"></span>Brimsett<br>Gardening</div>
  <div class="social" style="left:156px"></div>
  <div class="social" style="left:190px"></div>
  <div class="social" style="left:225px"></div>
  <div class="social" style="left:259px"></div>

  <div class="f-head" style="left:512px">Quick Links</div>
  <div class="f-rule" style="left:512px;width:86px"></div>
  <div class="f-link" style="top:102px">Home</div>
  <div class="f-link" style="top:138px">Services</div>
  <div class="f-link" style="top:173px">Gallery</div>
  <div class="f-link" style="top:209px">About Us</div>
  <div class="f-link" style="top:244px">Contact Us</div>

  <div class="f-head" style="left:848px">Contact Details</div>
  <div class="f-rule" style="left:848px;width:152px"></div>
  <div class="contact" style="top:95px">
    <svg width="28" height="28" viewBox="0 0 28 28" fill="none" stroke="#fff" stroke-width="1.4"><circle cx="12" cy="15" r="10"/><path d="M2 15h20M12 5c-4 5-4 15 0 20M12 5c4 5 4 15 0 20"/><path d="M22 3a4 4 0 0 0-4 4c0 3 4 7 4 7s4-4 4-7a4 4 0 0 0-4-4z" fill="#1e1e1e"/></svg>
    <div>123, Building Name, Street<br>City, State XY 123456</div>
  </div>
  <div class="contact" style="top:157px">
    <svg width="28" height="28" viewBox="0 0 28 28" fill="none" stroke="#fff" stroke-width="1.4"><path d="M5 5l5 5-2.5 3c2 3.5 4 5.5 7.5 7.5l3-2.5 5 5-3 3C11 25 3 17 3 7z"/><circle cx="21" cy="7" r="5"/><path d="M19 7l1.5 1.5L23 5.5"/></svg>
    <div><b>Phone</b>(123) 456-7890</div>
  </div>
  <div class="contact" style="top:219px">
    <svg width="28" height="28" viewBox="0 0 28 28" fill="none" stroke="#fff" stroke-width="1.4"><path d="M3 11l11-8 11 8v14H3z"/><path d="M3 11l11 8 11-8"/><path d="M8 9h12v6"/></svg>
    <div><b>Email</b>info@brimsettgardening.com</div>
  </div>

  <div class="f-divider"></div>
  <div class="copyright">© 2024 Brimsett Gardening. All Rights Reserved</div>
</footer>

</body>
</html>
```